BQR, LLC Original

I need a business card design for a new company in Gaithersburg, MD. Though the name of the company is Wiremasters Of Northfield (BQR) we specialize in commercial kitchen ventilation systems as a complete turnkey project or as a service provider. We can design the entire system including the hoods, fans, ductwork, and fire system. We also specialize in fire alarm service, design, install and inspection. We are experts on any Ventaro Dynamics equipment including Pulsar VXM, Pulsar Canopies, EMS controls, Standard controls, PCU filtration and Make-up Air units with heaters and cooling. We can repair/retrofit old water wash hood systems as well. We are experts with local code requirements and upgrades.

Industry/Entity Type

Business

Contact Information for Business Card

Dale Pruitt, Wiremasters Of Northfield, LLC; 240-555-0187 Cell, Brookhaven, MD 20990. Dalep@wiremastersnorthfield.example

```html
<!DOCTYPE html>
<html lang="en">
<head>
<meta charset="utf-8">
<title>Wiremasters Of Northfield – Business Card</title>
<link rel="stylesheet" href="https://fonts.googleapis.com/css2?family=Questrial&display=swap">
<style>
  :root {
    --paper: #ffffff;
    --red: #e8333a;
    --ink: #3d3d3d;
    --frame: #555555;
    --guide: #6a6a6a;
  }
  html, body {
    margin: 0;
    padding: 0;
    width: 1200px;
    height: 751px;
    overflow: hidden;
    background: var(--paper);
  }
  .card {
    position: relative;
    width: 1200px;
    height: 751px;
    box-sizing: border-box;
    border: 2px solid var(--frame);
    background: var(--paper);
    font-family: "Questrial", "Century Gothic", sans-serif;
    overflow: hidden;
  }
  .safe-area {
    position: absolute;
    left: 48px;
    top: 34px;
    width: 1110px;
    height: 686px;
    border: 2px dotted var(--guide);
    box-sizing: border-box;
  }
  .contact-band {
    position: absolute;
    left: 49px;
    top: 529px;
    width: 1108px;
    height: 190px;
    background: var(--red);
  }
  .brand-name {
    position: absolute;
    left: 0;
    top: 142px;
    width: 1210px;
    text-align: center;
    color: var(--red);
    font-weight: 400;
    text-transform: uppercase;
    line-height: 1;
  }
  .brand-name .line-main {
    display: block;
    font-size: 80px;
    letter-spacing: 2px;
  }
  .brand-name .line-sub {
    display: block;
    margin-top: 10px;
    font-size: 44px;
    letter-spacing: 4px;
  }
  .services {
    position: absolute;
    left: 0;
    top: 312px;
    width: 1208px;
    margin: 0;
    text-align: center;
    color: var(--red);
    font-size: 31px;
    line-height: 37px;
    -webkit-text-stroke: 0.6px var(--red);
  }
  .person-name {
    position: absolute;
    left: 0;
    top: 454px;
    width: 1208px;
    margin: 0;
    text-align: center;
    color: var(--ink);
    font-size: 58px;
    font-weight: 400;
    line-height: 1.2;
    -webkit-text-stroke: 0.8px var(--ink);
  }
  .contact-list {
    position: absolute;
    left: 0;
    top: 563px;
    width: 1130px;
    margin: 0;
    padding: 0;
    list-style: none;
    color: var(--ink);
    font-size: 34px;
    -webkit-text-stroke: 0.6px var(--ink);
  }
  .contact-item {
    display: flex;
    justify-content: center;
    align-items: center;
    gap: 36px;
    height: 44px;
  }
  .contact-icon {
    flex: none;
    fill: var(--ink);
  }
</style>
</head>
<body>
  <div class="card">
    <div class="contact-band"></div>
    <div class="safe-area"></div>

    <div class="brand-name">
      <span class="line-main">Wiremasters</span>
      <span class="line-sub">Of Northfield</span>
    </div>

    <p class="services">Entire system including the hoods, fans, ductwork, and fire system.<br>specialize in fire alarm service, design, install and inspection.</p>

    <h1 class="person-name">Dale Pruitt</h1>

    <ul class="contact-list">
      <li class="contact-item">
        <svg class="contact-icon" width="20" height="40" viewBox="0 0 20 40" aria-hidden="true">
          <rect x="3" y="0" width="2.5" height="10"/>
          <rect x="1" y="9" width="18" height="31" rx="3"/>
          <rect x="4" y="12" width="12" height="9" fill="#e8333a"/>
          <g fill="#e8333a">
            <rect x="4" y="24" width="3" height="2.5"/><rect x="8.5" y="24" width="3" height="2.5"/><rect x="13" y="24" width="3" height="2.5"/>
            <rect x="4" y="28.5" width="3" height="2.5"/><rect x="8.5" y="28.5" width="3" height="2.5"/><rect x="13" y="28.5" width="3" height="2.5"/>
            <rect x="4" y="33" width="3" height="2.5"/><rect x="8.5" y="33" width="3" height="2.5"/><rect x="13" y="33" width="3" height="2.5"/>
          </g>
        </svg>
        <span>240-555-0187</span>
      </li>
      <li class="contact-item">
        <svg class="contact-icon" width="40" height="26" viewBox="0 0 40 26" aria-hidden="true">
          <path d="M0 0h40v26H0z M3 3l17 13L37 3 M3 23l12-10 M37 23L25 13" fill="#3d3d3d" stroke="#e8333a" stroke-width="2"/>
        </svg>
        <span>dalep@wiremastersnorthfield.example</span>
      </li>
      <li class="contact-item">
        <svg class="contact-icon" width="24" height="34" viewBox="0 0 24 34" aria-hidden="true">
          <path d="M12 0C5.4 0 0 5.3 0 11.8 0 20.5 12 34 12 34s12-13.5 12-22.2C24 5.3 18.6 0 12 0zm0 16.5a4.8 4.8 0 1 1 0-9.6 4.8 4.8 0 0 1 0 9.6z"/>
        </svg>
        <span>Brookhaven, MD 20990</span>
      </li>
    </ul>
  </div>
</body>
</html>
```